Animal Horse & Bedding Company Needs a Website Coded & Designed

We need a website for a new animal bedding and feed company that is visually grabbing and vibrant. We would like to see a website that displays trust, quality and confidence. Needs to be responsive and mobile friendly for all browsers and coded for both Android & IOS. SEO is also important.

Joomla or Wordpress – must be both desktop and mobile friendly with fast page load speed. Need the ability to edit ourselves in Wordpress or Joomla.

Full details attached below with some layout and content ideas.

Coding

Coded - Design and coding required

Number of Pages Required

5+ page

Font styles to use
Sans Serif

Requirements
Must have
• Needs to be responsive and mobile friendly for all browsers and coded for both Android & IOS. SEO is also important.

Wordpress – must be both desktop and mobile friendly with fast page load speed. Need the ability to edit ourselves in Wordpress.

Logo Colours:
Dark Brown
CMYK: 50 / 70 / 80 / 70
Pantone: 4625C

Orange
CMYK: 0 / 50 / 100 / 0
Pantone: 144C
Nice to have
• Use picture of building attached and super impose logo on building.

```html
<!DOCTYPE html>
<html lang="en">
<head>
<meta charset="utf-8">
<title>Golden Stalk Bedding &amp; Feed</title>
<link href="https://fonts.googleapis.com/css2?family=Oswald:wght@300;400&family=Poppins:wght@400;500;600;700&display=swap" rel="stylesheet">
<style>
:root{
  --orange:#f7941d;
  --orange-deep:#ef8a12;
  --brown:#3f1f0e;
  --brown-mid:#4b2613;
  --cream:#faf7f0;
  --text:#3a3a3a;
  --muted:#6b6b6b;
  --white:#ffffff;
}
*{margin:0;padding:0;box-sizing:border-box}
html,body{width:1200px;height:3968px;overflow:hidden}
body{position:relative;font-family:'Poppins',sans-serif;color:var(--text);background:var(--white)}
.abs{position:absolute}
.display{font-family:'Oswald',sans-serif;font-weight:300;letter-spacing:1px}

/* header */
.site-header{left:0;top:0;width:1200px;height:95px;background:var(--white)}
.brand{left:97px;top:22px;display:flex;align-items:center;gap:12px}
.brand-dot{width:44px;height:44px;border-radius:50%;background:var(--orange)}
.brand-name{font-family:'Oswald',sans-serif;font-weight:400;font-size:30px;color:var(--brown);letter-spacing:2px}
.main-nav{top:43px;left:0;font-size:12px;font-weight:500;color:var(--brown)}
.main-nav a{position:absolute;white-space:nowrap;color:var(--brown);text-decoration:none}
.main-nav a.active{color:var(--orange)}
.btn{display:flex;align-items:center;justify-content:center;font-weight:700;text-transform:uppercase;text-decoration:none}
.btn-quote{left:950px;top:30px;width:154px;height:38px;border-radius:19px;background:var(--orange);color:var(--white);font-size:12px}

/* hero */
.hero{left:0;top:95px;width:1200px;height:611px;background:linear-gradient(180deg,#6e7a3a 0%,#8b8446 45%,#b3a063 75%,#c7a86d 100%)}
.hero-photo{left:0;top:0;width:1200px;height:611px;background:radial-gradient(ellipse 260px 300px at 760px 300px,#9a4a1c 0%,rgba(154,74,28,0.6) 55%,rgba(154,74,28,0) 100%)}
.hero-badge{left:98px;top:167px;width:420px;height:420px;border-radius:50%;background:rgba(247,148,29,0.93);text-align:center;color:var(--white)}
.hero-badge .welcome{margin-top:120px;font-size:36px}
.hero-badge .title{font-size:62px;line-height:1.1;font-weight:400}
.hero-badge .sub{font-size:24px;letter-spacing:6px}
.btn-learn{margin:14px auto 0;width:156px;height:42px;border-radius:20px 0 20px 0;background:var(--brown);color:var(--white);font-size:12px}
.hero-dots{left:572px;top:666px;display:flex;gap:9px}
.hero-dots span{width:11px;height:11px;border-radius:50%;background:var(--white)}

/* about */
.about{left:0;top:706px;width:1200px;height:792px;background:var(--cream)}
.about-photo{left:428px;top:49px;width:667px;height:477px;background:linear-gradient(180deg,#b9c8d4 0%,#4f6a3a 25%,#6f7f48 45%,#a52a2a 60%,#b8b8b0 80%,#8a8a7d 100%)}
.about-card{left:103px;top:92px;width:545px;height:387px;background:var(--brown)}
.about-card .frame{position:absolute;left:12px;top:12px;right:12px;bottom:12px;border:1px solid #8a6a55}
.about-card h2{position:absolute;top:50px;width:100%;text-align:center;color:var(--white);font-size:38px}
.rule{height:3px;width:40px;background:var(--orange)}
.about-card .rule{position:absolute;left:252px;top:104px}
.about-card .copy{position:absolute;left:65px;right:65px;top:130px;color:#efe5dc;font-size:11px;line-height:15.5px;text-align:center}
.about-card .copy p{margin-bottom:15px}
.features{left:0;top:635px;width:1200px;height:120px}
.feature{position:absolute;top:0}
.feature h3{font-size:16px;font-weight:500;color:var(--brown);line-height:22px;text-transform:uppercase}
.feature p{margin-top:10px;font-size:11px;color:var(--muted);line-height:19px}
.feature-icon{position:absolute;top:2px}
.divider{position:absolute;top:10px;width:1px;height:110px;background:#ddd}

/* bedding */
.bedding{left:0;top:1498px;width:1200px;height:876px;background:var(--white)}
.section-title{font-size:44px;color:var(--brown);text-align:center}
.bedding .section-title{position:absolute;top:70px;width:100%}
.bedding .rule{position:absolute;left:580px;top:130px}
.bed-photo{left:436px;top:175px;width:332px;height:332px;border-radius:50%;border:9px solid var(--orange);background:radial-gradient(circle at 50% 40%,#8a4a24 0%,#7a5a3a 45%,#b9a27a 100%)}
.benefit-icon{width:76px;height:76px;border-radius:50%;display:flex;align-items:center;justify-content:center}
.benefit-icon.o{background:var(--orange)}
.benefit-icon.d{background:var(--brown)}
.benefit-label{font-size:14px;line-height:19px;color:var(--text);font-weight:500}
.right{text-align:right}
.btn-view{width:189px;height:52px;border-radius:24px 0 24px 0;background:var(--brown);color:var(--white);font-size:14px}

/* feed */
.feed{left:0;top:2374px;width:1200px;height:612px;background:var(--orange);overflow:hidden}
.feed-photo{left:0;top:0;width:1200px;height:612px}
.feed h2{position:absolute;left:112px;top:60px;font-size:46px;color:var(--white);font-weight:300}
.feed .rule{position:absolute;left:115px;top:122px;background:var(--brown)}
.feed .intro{position:absolute;left:115px;top:134px;width:460px;color:var(--white);font-size:12.5px;line-height:21px}
.feed-item{position:absolute;display:flex;align-items:center;gap:8px;color:var(--white);font-size:10px;font-weight:700;line-height:12px}
.feed .btn-view{position:absolute;left:120px;top:497px;width:173px}

/* delivery */
.delivery{left:0;top:2986px;width:1200px;height:568px;background:var(--white)}
.map{left:133px;top:118px;width:475px;height:386px;background:linear-gradient(180deg,var(--brown-mid) 0%,var(--brown-mid) 42%,var(--orange-deep) 43%,#f2a010 100%);border-radius:30px 120px 80px 160px}
.delivery h2{position:absolute;left:652px;top:170px;font-size:40px;color:var(--brown)}
.delivery .rule{position:absolute;left:658px;top:229px}
.delivery .copy{position:absolute;left:659px;top:257px;width:420px;font-size:12.5px;line-height:21px;color:var(--muted)}
.delivery .copy p{margin-bottom:10px}
.btn-contact{position:absolute;left:653px;top:372px;width:153px;height:44px;border:1px solid var(--orange);border-radius:22px 0 22px 0;color:var(--orange);font-size:12px}

/* footer */
.site-footer{left:0;top:3554px;width:1200px;height:414px;background:var(--brown);color:var(--white)}
.foot-brand{left:118px;top:100px;width:234px;text-align:center}
.foot-brand .brand-dot{margin:0 auto 12px;width:50px;height:50px}
.foot-brand .name{font-family:'Oswald',sans-serif;font-size:34px;letter-spacing:2px;color:var(--white)}
.socials{left:167px;top:211px;display:flex;gap:7px}
.socials span{width:32px;height:32px;border-radius:50%;background:var(--white)}
.socials span:first-child{background:var(--orange)}
.foot-col h4{font-size:14px;font-weight:500;text-transform:uppercase;margin-bottom:14px}
.foot-col .link,.foot-col .line{display:block;font-size:11.5px;line-height:26px;color:#e8dcd2;text-decoration:none}
.foot-col .contact-row{display:flex;gap:12px;align-items:flex-start;margin-bottom:4px}
.foot-col .contact-row svg{flex:none;margin-top:5px}
.newsletter input{display:block;width:231px;height:36px;border-radius:18px;border:1px solid #9a7a66;background:transparent;color:var(--white);padding-left:20px;font-family:inherit;font-size:11px}
.newsletter input::placeholder{color:#e8dcd2}
.foot-col .btn-sub{display:flex;margin:22px 0 0 6px;width:132px;height:33px;border-radius:17px;background:var(--orange);color:var(--white);font-size:11px}
.copyright{left:0;top:362px;width:1200px;text-align:center;font-size:10px;color:#d7c6b9}
</style>
</head>
<body>

<header class="site-header abs">
  <div class="brand abs"><span class="brand-dot"></span><span class="brand-name">GOLDEN STALK</span></div>
  <nav class="main-nav abs">
    <a class="active" style="left:453px">HOME</a>
    <a style="left:539px">ABOUT</a>
    <a style="left:630px">FEED</a>
    <a style="left:709px">BEDDING</a>
    <a style="left:813px">CONTACT US</a>
  </nav>
  <a class="btn btn-quote abs">Request Quote &#8250;</a>
</header>

<section class="hero abs" role="img" aria-label="Chestnut horse standing in a summer meadow">
  <div class="hero-photo abs"></div>
  <div class="hero-badge abs">
    <div class="welcome display">WELCOME TO</div>
    <div class="title display">GOLDEN STALK</div>
    <div class="sub display">BEDDING &amp; FEED</div>
    <a class="btn btn-learn">Learn More &#8250;</a>
  </div>
  <div class="hero-dots abs"><span></span><span></span><span></span></div>
</section>

<section class="about abs">
  <div class="about-photo abs" role="img" aria-label="Aerial view of red barns and fenced paddocks"></div>
  <div class="about-card abs">
    <div class="frame"></div>
    <h2 class="display">ABOUT GOLDEN STALK</h2>
    <div class="rule"></div>
    <div class="copy">
      <p>Looking for the best bedding and feed for your horse, livestock or household pet look no further. We use premium locally sourced straw and hay in all of our products and are committed in providing quality products and service.</p>
      <p>Your animal deserves the very best in health and comfort to keep them healthy, strong and happy. Our products are designed for horses, livestock (goats, cattle and sheep), small caged animals (rabbits, guinea pigs and more).</p>
      <p>Golden Stalk offers supply and delivery of fresh bedding as well as removal of waste bedding. Let us deliver you a container of fresh straw and haul your waste bedding away. A full service solution that is sustainable and responsible.</p>
    </div>
  </div>
  <div class="features abs">
    <svg class="feature-icon" style="left:113px" width="46" height="66" viewBox="0 0 46 66" fill="none" stroke="#f7941d" stroke-width="2"><circle cx="23" cy="23" r="20"/><circle cx="23" cy="23" r="13"/><path d="M12 40 L6 62 L14 57 L18 64 L23 44 M34 40 L40 62 L32 57 L28 64 L23 44"/></svg>
    <div class="feature" style="left:169px"><h3>Quality<br>Guaranteed</h3><p>Grown for quality - 100% natural with no<br>chemicals or additives</p></div>
    <div class="divider" style="left:431px"></div>
    <svg class="feature-icon" style="left:460px" width="54" height="54" viewBox="0 0 54 54" fill="none" stroke="#f7941d" stroke-width="2.5"><path d="M8 10 A24 24 0 1 0 46 10"/><path d="M17 17 L37 37 M37 17 L17 37"/></svg>
    <div class="feature" style="left:527px"><h3>Full Service<br>Solution</h3><p>Dedicated in providing a full service solution<br>of bedding supply &amp; waste removal</p></div>
    <div class="divider" style="left:801px"></div>
    <svg class="feature-icon" style="left:822px" width="60" height="58" viewBox="0 0 60 58" fill="none" stroke="#f7941d" stroke-width="2"><ellipse cx="30" cy="34" rx="24" ry="17"/><circle cx="33" cy="12" r="8"/><path d="M14 48 L14 56 M42 48 L42 56"/></svg>
    <div class="feature" style="left:893px"><h3>Convenient &amp; Cost<br>Effective</h3><p>Compressed bags , pellets or bulk products<br>saving in shipping costs</p></div>
  </div>
</section>

<section class="bedding abs">
  <h2 class="section-title display">BEDDING</h2>
  <div class="rule"></div>
  <div class="bed-photo abs" role="img" aria-label="Horse resting on straw bedding"></div>

  <svg class="abs" style="left:0;top:0" width="1200" height="876" fill="none" stroke="#9a9a9a" stroke-width="1.5">
    <path d="M445 240 Q425 205 388 203 M388 203 l8 -5 M388 203 l7 6"/>
    <path d="M760 240 Q780 205 818 205 M818 205 l-8 -5 M818 205 l-7 6"/>
    <path d="M432 402 Q412 440 368 432 M368 432 l8 -6 M368 432 l7 6"/>
    <path d="M768 412 Q788 446 832 437 M832 437 l-8 -6 M832 437 l-7 6"/>
    <path d="M508 505 Q490 530 445 535 M445 535 l8 -6 M445 535 l7 6"/>
    <path d="M676 518 Q700 540 740 543 M740 543 l-8 -6 M740 543 l-7 6"/>
    <path d="M601 573 L601 628 M601 628 l-6 -8 M601 628 l6 -8"/>
  </svg>

  <div class="benefit-icon o abs" style="left:284px;top:175px"><svg width="30" height="38" viewBox="0 0 30 38" fill="none" stroke="#fff" stroke-width="2"><path d="M15 2 C28 12 28 28 15 34 C2 28 2 12 15 2 Z M15 10 L15 38"/></svg></div>
  <div class="benefit-label right abs" style="left:120px;top:194px;width:148px">100% Natural<br>Chopped Straw</div>

  <div class="benefit-icon o abs" style="left:843px;top:175px"><svg width="38" height="36" viewBox="0 0 38 36" fill="none" stroke="#fff" stroke-width="2"><path d="M19 4 L10 18 M19 4 L28 18 M6 26 L32 26 M10 18 L6 26 M28 18 L32 26"/></svg></div>
  <div class="benefit-label abs" style="left:934px;top:196px;width:220px">Environmentally Friendly –<br>Recyclable &amp; Compostable</div>

  <div class="benefit-icon d abs" style="left:301px;top:351px"><svg width="38" height="38" viewBox="0 0 38 38" fill="none" stroke="#fff" stroke-width="2"><circle cx="19" cy="19" r="16"/><path d="M8 8 L30 30"/></svg></div>
  <div class="benefit-label right abs" style="left:160px;top:378px;width:125px">Low Dust</div>

  <div class="benefit-icon d abs" style="left:818px;top:351px"><svg width="38" height="38" viewBox="0 0 38 38" fill="none" stroke="#fff" stroke-width="2"><circle cx="19" cy="19" r="16"/><path d="M3 19 L35 19 M19 3 C10 12 10 26 19 35 C28 26 28 12 19 3"/></svg></div>
  <div class="benefit-label abs" style="left:905px;top:370px;width:200px">Economic – less used<br>and less wasted</div>

  <div class="benefit-icon o abs" style="left:365px;top:520px"><svg width="38" height="38" viewBox="0 0 38 38" fill="none" stroke="#fff" stroke-width="2"><circle cx="19" cy="19" r="16"/><path d="M15 8 L15 16 L9 28 L29 28 L23 16 L23 8"/></svg></div>
  <div class="benefit-label right abs" style="left:212px;top:536px;width:140px">Chemical &amp;<br>Additive Free</div>

  <div class="benefit-icon o abs" style="left:752px;top:520px"><svg width="42" height="30" viewBox="0 0 42 30" fill="none" stroke="#fff" stroke-width="2"><path d="M3 24 L39 24 L35 12 L7 12 Z M16 12 L20 4"/></svg></div>
  <div class="benefit-label abs" style="left:839px;top:536px;width:150px">Cheaper than<br>Wood Shavings</div>

  <div class="benefit-icon d abs" style="left:563px;top:600px"><svg width="40" height="40" viewBox="0 0 40 40" fill="none" stroke="#fff" stroke-width="2"><circle cx="14" cy="24" r="8"/><circle cx="26" cy="14" r="6"/><circle cx="27" cy="30" r="4"/></svg></div>
  <div class="benefit-label abs" style="left:501px;top:685px;width:200px;text-align:center">Clean &amp; Highly<br>Absorbent</div>

  <a class="btn btn-view abs" style="left:519px;top:764px">View Bedding &nbsp;&#8250;</a>
</section>

<section class="feed abs">
  <svg class="feed-photo abs" width="1200" height="612" viewBox="0 0 1200 612" role="img" aria-label="Man feeding a horse from a metal bucket at a paddock fence">
    <defs><linearGradient id="feedPhoto" x1="0" y1="0" x2="1" y2="1"><stop offset="0" stop-color="#a9ad9a"/><stop offset="0.5" stop-color="#6b4a2e"/><stop offset="1" stop-color="#4d3a2a"/></linearGradient></defs>
    <path d="M735 0 L1200 0 L1200 612 L620 612 Q630 260 735 0 Z" fill="url(#feedPhoto)"/>
  </svg>
  <h2 class="display">OUR FEED</h2>
  <div class="rule"></div>
  <p class="intro">Hay cubes and pellets are made from premium hay offering a variety of animals a feed that is non-GMO and packed with natural nutrients. These pellets and cubes are less bulky to handle, store and ship. As well, they reduce the amount of wasted feed.</p>

  <div class="feed-item" style="left:116px;top:248px"><svg width="22" height="32" viewBox="0 0 22 32" fill="none" stroke="#fff" stroke-width="1.6"><path d="M11 2 C21 10 21 22 11 27 C1 22 1 10 11 2 Z M11 8 L11 31"/></svg>100% Natural</div>
  <div class="feed-item" style="left:297px;top:248px"><svg width="34" height="34" viewBox="0 0 34 34" fill="none" stroke="#fff" stroke-width="1.6"><circle cx="17" cy="17" r="15"/><path d="M14 7 L14 14 L8 25 L26 25 L20 14 L20 7"/></svg>Chemical &amp;<br>Additive Free</div>
  <div class="feed-item" style="left:451px;top:248px"><svg width="40" height="34" viewBox="0 0 40 34" fill="none" stroke="#fff" stroke-width="1.6"><path d="M4 12 L14 7 L24 12 L14 17 Z M4 12 L4 24 L14 29 L14 17 M24 12 L24 24 L14 29 M20 18 L30 13 L38 17 L38 28 L28 32"/></svg>Available in<br>Pellets or Cubes</div>

  <div class="feed-item" style="left:112px;top:326px"><svg width="36" height="34" viewBox="0 0 36 34" fill="none" stroke="#fff" stroke-width="1.6"><circle cx="10" cy="20" r="7"/><circle cx="24" cy="10" r="5"/><circle cx="26" cy="26" r="4"/></svg>Clean - Eliminates<br>Dust From Feeding<br>Baled Hay</div>
  <div class="feed-item" style="left:297px;top:326px"><svg width="34" height="38" viewBox="0 0 34 38" fill="none" stroke="#fff" stroke-width="1.6"><path d="M6 8 L28 8 L25 36 L9 36 Z M4 8 L30 8 M13 3 L21 3 M13 14 L13 30 M21 14 L21 30"/></svg>Eliminate Waste<br>In Feeding</div>
  <div class="feed-item" style="left:458px;top:328px"><svg width="34" height="32" viewBox="0 0 34 32" fill="none" stroke="#fff" stroke-width="1.6"><path d="M4 24 C12 4 22 4 30 8 M8 28 C16 12 24 12 30 16 M14 30 C20 20 26 20 30 24"/></svg>High Protein<br>Content</div>

  <div class="feed-item" style="left:108px;top:398px"><svg width="40" height="36" viewBox="0 0 40 36" fill="none" stroke="#fff" stroke-width="1.6"><circle cx="16" cy="16" r="13"/><path d="M20 10 C12 8 12 16 16 16 C20 16 20 24 12 22 M16 6 L16 26"/><circle cx="32" cy="28" r="5"/></svg>Cost Effective</div>
  <div class="feed-item" style="left:292px;top:398px"><svg width="38" height="38" viewBox="0 0 38 38" fill="none" stroke="#fff" stroke-width="1.6"><path d="M32 12 A16 16 0 1 1 26 5"/><path d="M11 19 L17 25 L33 7"/></svg>Convenient</div>
  <div class="feed-item" style="left:458px;top:400px"><svg width="34" height="34" viewBox="0 0 34 34" fill="none" stroke="#fff" stroke-width="1.6"><path d="M17 3 L10 15 M17 3 L24 15 M5 24 L29 24 M10 15 L5 24 M24 15 L29 24 M12 30 L22 30"/></svg>Less wasted<br>feed</div>

  <a class="btn btn-view">View Feed &nbsp;&#8250;</a>
</section>

<section class="delivery abs">
  <div class="map abs" role="img" aria-label="Map of Canada in brown and the United States in orange"></div>
  <h2 class="display">DELIVERY IN CANADA &amp; USA</h2>
  <div class="rule"></div>
  <div class="copy">
    <p>Looking for the best bedding and feed for your horse, livestock or household pet look no further.</p>
    <p>We use premium locally sourced straw and hay in all of our products and are committed in providing quality products and service.</p>
  </div>
  <a class="btn btn-contact">Contact Us</a>
</section>

<footer class="site-footer abs">
  <div class="foot-brand abs">
    <div class="brand-dot"></div>
    <div class="name">GOLDEN STALK</div>
  </div>
  <div class="socials abs" aria-label="Social links"><span></span><span></span><span></span><span></span></div>

  <div class="foot-col abs" style="left:427px;top:92px">
    <h4>Sitemap</h4>
    <a class="link">Home</a><a class="link">About Us</a><a class="link">Our Bedding</a><a class="link">Feed</a><a class="link">Contact Us</a>
  </div>

  <div class="foot-col abs" style="left:602px;top:92px">
    <h4>Contact Us</h4>
    <div class="contact-row"><svg width="14" height="18" viewBox="0 0 14 18"><path d="M7 0 C3 0 0 3 0 7 C0 12 7 18 7 18 C7 18 14 12 14 7 C14 3 11 0 7 0 Z" fill="#f7941d"/><circle cx="7" cy="7" r="2.5" fill="#3f1f0e"/></svg><div class="line">48 Meadow Lane, Fieldtown<br>40817, Northland</div></div>
    <div class="contact-row"><svg width="14" height="14" viewBox="0 0 14 14"><path d="M3 1 L5 4 L4 6 C5 8 6 9 8 10 L10 9 L13 11 L12 13 C6 13 1 8 1 2 Z" fill="#f7941d"/></svg><div class="line">(555) 010-4821</div></div>
    <div class="contact-row" style="margin-top:10px"><svg width="16" height="12" viewBox="0 0 16 12"><rect width="16" height="12" fill="#f7941d"/><path d="M0 0 L8 7 L16 0" stroke="#3f1f0e" fill="none"/></svg><div class="line">hello@goldenstalk.example</div></div>
  </div>

  <div class="foot-col newsletter abs" style="left:864px;top:88px">
    <h4>Newsletter Sign Up</h4>
    <input type="email" placeholder="Email address">
    <a class="btn btn-sub">Subscribe</a>
  </div>

  <div class="copyright abs">© Copyright 2020 . Golden Stalk . All Right Reserved</div>
</footer>

</body>
</html>
```